Real estate agent website

I am a new real estate agent and in of a simple but powerful website that is linked to the local Multiple listing services (MLS). It should have a lending page that is connected to my customer relationship management (CRM) software. It must have an ability for potential customers to search for properties and be able to communicate with me easily.
Updates

Updates: The website themes must includes MLS-IDX integration with a grid layout and property slider so i can showcase featured properties. I also would like to have future where potential client can search and have alerts depending on a search criteria.

Industry/Entity Type

Real Estate

Coding

Coded - Design and coding required

Number of Pages Required

3 page

Requirements
Must have
• Home page, Resources page, About Me with contact me window page

```html
<!DOCTYPE html>
<html lang="en">
<head>
<meta charset="utf-8">
<title>Marina Hollis – Real Estate Agent</title>
<link href="https://fonts.googleapis.com/css2?family=Poppins:ital,wght@0,400;0,500;0,600;0,700;1,700&display=swap" rel="stylesheet">
<style>
:root{
  --slate:#4a4d59;
  --teal:#2b9488;
  --orange:#e08b2a;
  --ink:#333;
  --white:#fff;
  --line:#cfcfcf;
}
*{box-sizing:border-box;margin:0;padding:0}
html,body{width:1200px;height:3499px;overflow:hidden}
body{font-family:'Poppins',sans-serif;color:var(--ink);background:var(--white);position:relative}
.btn{display:inline-flex;align-items:center;justify-content:center;background:var(--orange);color:var(--white);font-weight:600;text-decoration:none}
/* header */
.site-header{position:absolute;top:0;left:0;width:1200px;height:129px;background:var(--slate);color:var(--white)}
.brand{position:absolute;left:75px;top:22px;display:flex;align-items:center;gap:10px}
.brand-mark{width:16px;height:16px;border-radius:50%;background:var(--orange);flex:none}
.brand-name{font-size:22px;font-weight:500;color:var(--white);white-space:nowrap}
.brand-tag{position:absolute;left:75px;top:92px;font-size:13px;color:#eee;white-space:nowrap}
.main-nav{position:absolute;left:372px;top:55px;display:flex;gap:39px;font-size:15px}
.main-nav a{color:var(--white);text-decoration:none}
.main-nav a.active{color:var(--orange);font-weight:600}
.call{position:absolute;left:985px;top:42px}
.call small{display:block;font-size:13px;font-weight:700}
.call strong{font-size:22px;font-weight:700}
/* hero */
.hero{position:absolute;top:129px;left:0;width:1200px;height:655px;background:linear-gradient(180deg,#6f8fb8 0%,#a6a8ac 35%,#8d857c 55%,#e6e9ee 72%,#f2f4f7 100%);text-align:center;color:var(--white)}
.hero h1{font-size:76px;font-weight:700;margin-top:180px;line-height:1}
.hero .role{font-size:32px;font-style:italic;font-weight:700;margin-top:16px}
.hero .tagline{font-size:40px;font-weight:600;margin-top:10px}
.hero .btn{width:160px;height:58px;font-size:18px;margin-top:22px}
/* search */
.search{position:absolute;top:784px;left:0;width:1200px;height:186px;background:var(--teal);text-align:center}
.search h2{color:var(--white);font-size:28px;font-weight:600;padding-top:42px}
.search-row{position:absolute;left:75px;top:96px;display:flex;gap:12px}
.field{height:45px;background:var(--white);border-radius:3px;font-size:13px;display:flex;align-items:center;justify-content:space-between;padding:0 14px;color:#333}
.field.loc{width:347px}
.field.sel{width:120px}
.search-row .btn{width:165px;height:45px;font-size:16px}
/* listings */
.featured{position:absolute;top:970px;left:0;width:1200px;height:658px}
.featured h2{text-align:center;font-size:46px;font-weight:700;color:#333;margin-top:67px}
.arrow{position:absolute;top:336px;width:42px;height:42px;border:1px solid #ccc;border-radius:50%;background:#fff;display:flex;align-items:center;justify-content:center}
.card{position:absolute;top:154px;width:329px}
.card .photo{height:238px;background:linear-gradient(180deg,#6a9ad0 0%,#b7c2cc 45%,#8e8577 65%,#eef0f3 100%)}
.card .street{font-size:18px;font-weight:600;margin-top:20px;color:#222}
.card .city{font-size:15px;margin-top:4px}
.card .price{font-size:24px;font-weight:700;color:var(--teal);margin-top:18px}
.card .btn{width:157px;height:46px;font-size:17px;margin-top:12px}
.specs{position:absolute;right:0;top:262px;text-align:center;font-size:12px;line-height:1.3}
.specs b{display:block;font-size:16px;margin-bottom:20px}
/* about */
.about{position:absolute;top:1628px;left:0;width:1200px;height:562px;background:var(--slate);color:var(--white)}
.portrait{position:absolute;left:75px;top:71px;width:421px;height:571px;background:#fff;padding:8px;box-shadow:0 8px 20px rgba(0,0,0,.25)}
.portrait div{width:100%;height:100%;background:linear-gradient(180deg,#d9d4cf 0%,#c79575 40%,#f4efea 80%)}
.about-text{position:absolute;left:525px;top:60px;width:600px}
.about-text h2{font-size:46px;font-weight:700;line-height:1}
.about-text h3{font-size:32px;font-weight:400;margin-top:8px}
.about-text p{font-size:15px;line-height:28px;margin-top:14px}
.about-text p+p{margin-top:12px}
.about-text p.tight{margin-top:0}
.about-text .btn{width:161px;height:60px;font-size:18px;margin-top:30px}
/* contact */
.contact{position:absolute;top:2347px;left:75px;width:1051px;height:459px;background:linear-gradient(160deg,#cfd3d6,#f4f5f7 40%,#8a8f8a 70%,#e8eaec);overflow:hidden}
.contact svg.band{position:absolute;left:0;top:0}
.contact-info{position:absolute;left:45px;top:45px;color:var(--white)}
.contact-info h2{font-size:46px;font-weight:700}
.item{display:flex;align-items:flex-start;gap:17px;font-size:17px;margin-top:22px;line-height:25px}
.item .ic{width:43px;height:43px;border-radius:50%;background:var(--orange);flex:none;display:flex;align-items:center;justify-content:center}
.contact-info .btn{width:160px;height:58px;font-size:17px;margin-top:30px}
/* email */
.email h2{position:absolute;top:2850px;width:1200px;text-align:center;font-size:46px;font-weight:700;color:#333}
.form{position:absolute;left:253px;top:2930px;width:694px}
.input{border:1px solid var(--line);height:57px;font-size:15px;padding:17px 16px;color:#555}
.row{display:flex;gap:15px}
.row .input{width:339px}
.form .full{margin-top:15px}
.form .msg{height:138px}
.form .btn{display:flex;width:340px;height:57px;margin:14px auto 0;font-size:18px}
/* footer */
.site-footer{position:absolute;top:3344px;left:0;width:1200px;height:155px;background:var(--slate);color:var(--white)}
.foot-nav{position:absolute;left:75px;top:56px;display:flex;gap:41px;font-size:16px}
.foot-nav a{color:var(--white);text-decoration:none}
.copy{position:absolute;left:75px;top:102px;font-size:13px}
.social{position:absolute;left:960px;top:58px;display:flex;gap:24px}
.social span{width:24px;height:24px;border-radius:4px;background:var(--white)}
</style>
</head>
<body>
<header class="site-header">
  <div class="brand"><span class="brand-mark"></span><span class="brand-name">Marina Hollis</span></div>
  <span class="brand-tag">CREATING RELATIONSHIPS THAT LAST</span>
  <nav class="main-nav">
    <a class="active" href="#">Home</a><a href="#">About Me</a><a href="#">Properties</a><a href="#">Lending</a><a href="#">Blog</a><a href="#">Contact Us</a>
  </nav>
  <div class="call"><small>CALL ME</small><strong>555-014-2290</strong></div>
</header>

<section class="hero" role="img" aria-label="Snowy townhouse exterior under a blue winter sky">
  <h1>Marina Hollis</h1>
  <p class="role">Real Estate Agent</p>
  <p class="tagline">Creating Relationships That Last</p>
  <a class="btn" href="#">View Listing</a>
</section>

<section class="search">
  <h2>SEARCH PROPERTIES</h2>
  <div class="search-row">
    <div class="field loc">Location, Zip code</div>
    <div class="field sel">Bed <span>⬍</span></div>
    <div class="field sel">Bath <span>⬍</span></div>
    <div class="field sel">Max <span>⬍</span></div>
    <div class="field sel">Min <span>⬍</span></div>
    <a class="btn" href="#">SEARCH</a>
  </div>
</section>

<section class="featured">
  <h2>FEATURED LISTINGS</h2>
  <div class="arrow" style="left:18px"><svg width="12" height="16" viewBox="0 0 12 16"><path d="M8 2 2 8l6 6" fill="none" stroke="#333" stroke-width="1.6"/></svg></div>
  <div class="arrow" style="left:1140px"><svg width="12" height="16" viewBox="0 0 12 16"><path d="M4 2l6 6-6 6" fill="none" stroke="#333" stroke-width="1.6"/></svg></div>

  <article class="card" style="left:75px">
    <div class="photo" role="img" aria-label="Two-storey townhouse with snow on the roof"></div>
    <p class="street">1847 Willow Ridge Drive</p><p class="city">Fairhaven, MN 55010</p>
    <p class="price">$330, 000</p><a class="btn" href="#">More Info</a>
    <div class="specs">Beds<b>3</b>Baths<b>4</b>Sqft<b>2361</b></div>
  </article>
  <article class="card" style="left:435px">
    <div class="photo" role="img" aria-label="Family home in a snowy yard"></div>
    <p class="street">1847 Willow Ridge Drive</p><p class="city">Fairhaven, MN 55010</p>
    <p class="price">$330, 000</p><a class="btn" href="#">More Info</a>
    <div class="specs">Beds<b>3</b>Baths<b>4</b>Sqft<b>2361</b></div>
  </article>
  <article class="card" style="left:798px">
    <div class="photo" role="img" aria-label="Split-level house with a lawn and trees" style="background:linear-gradient(180deg,#3f79c8 0%,#9fb6cf 45%,#8f8568 70%,#7d8a55 100%)"></div>
    <p class="street">1847 Willow Ridge Drive</p><p class="city">Fairhaven, MN 55010</p>
    <p class="price">$330, 000</p><a class="btn" href="#">More Info</a>
    <div class="specs">Beds<b>3</b>Baths<b>4</b>Sqft<b>2361</b></div>
  </article>
</section>

<section class="about">
  <div class="portrait"><div role="img" aria-label="Portrait photo of the agent"></div></div>
  <div class="about-text">
    <h2>ABOUT MARINA HOLLIS</h2>
    <h3>Realty Group, Inc</h3>
    <p>Purchasing or selling a house is the biggest investment venture that most of us will have in our lifetime. A home is a place of comfort and love.</p>
    <p class="tight">It is where we create memories. A place to live with our families and pets and enjoy our friends, and it’s a place where we create life-long memories.</p>
    <p>No matter what your goal or needs are in real estate, I would be honored to guide you through this journey. This is never just a business transaction; it will be a time where we would learn how to buildtrust that will sail our “ship” of relations throughout the years.</p>
    <a class="btn" href="#">READ MORE</a>
  </div>
</section>

<section class="contact" role="img" aria-label="Aerial view of a house among snowy woodland">
  <svg class="band" width="1051" height="459" viewBox="0 0 1051 459"><polygon points="0,0 628,0 450,459 0,459" fill="#2b9488"/></svg>
  <div class="contact-info">
    <h2>CONTACT US</h2>
    <div class="item"><span class="ic"><svg width="16" height="16" viewBox="0 0 16 16"><path d="M8 1a5 5 0 0 0-5 5c0 4 5 9 5 9s5-5 5-9a5 5 0 0 0-5-5zm0 7a2 2 0 1 1 0-4 2 2 0 0 1 0 4z" fill="#fff"/></svg></span><span>4120 Cedar Lane Ste 310, Brookfield,<br>Mn, 55000</span></div>
    <div class="item" style="align-items:center"><span class="ic"><svg width="16" height="16" viewBox="0 0 16 16"><path d="M4 1l3 3-2 2a9 9 0 0 0 5 5l2-2 3 3-2 3C7 15 1 9 1 3z" fill="#fff"/></svg></span><span>(555) 014-2290</span></div>
    <div class="item" style="align-items:center"><span class="ic"><svg width="16" height="12" viewBox="0 0 16 12"><rect width="16" height="12" rx="1" fill="#fff"/><path d="M1 1l7 5 7-5" fill="none" stroke="#e08b2a" stroke-width="1.5"/></svg></span><span>hello@hollishomes.com</span></div>
    <a class="btn" href="#">CONTACT US</a>
  </div>
</section>

<section class="email">
  <h2>EMAIL MARINA HOLLIS</h2>
  <form class="form">
    <div class="row"><div class="input">Enter Name</div><div class="input">Phone No</div></div>
    <div class="input full">Email Address</div>
    <div class="input full msg">Message</div>
    <a class="btn" href="#">SUBMIT NOW</a>
  </form>
</section>

<footer class="site-footer">
  <nav class="foot-nav"><a href="#">Home</a><a href="#">About Me</a><a href="#">Properties</a><a href="#">Lending</a><a href="#">Blog</a><a href="#">Contact Us</a></nav>
  <p class="copy">© 2023 Company Name All Right Reserved</p>
  <div class="social" aria-label="Social links"><span></span><span></span><span></span><span></span></div>
</footer>
</body>
</html>
```